Business Landing Page for SEO Company

Need the landing page of the website designed - I will provide the copy, will need to include details of my company and the services offered, about us, testimonials, faq, etc., and all these elements will need to be arranged graphically on the page.

I want something similar to this: https://torvanequill.com/

Not in terms of color or theme or anything, but we offer a similar service and want to display similar information.

Th services we provide are:

Premium Links
Monthly Links Subscription
Link Insertions

Need to advertise them on the front page. Additionally need a place for testimonials, company details, etc.,

We already have logo for the website. Please use the attached file to insert the logo within the overal design.

Target Market(s)

SEO marketers and agencies

Number of Pages Required

1 page

```html
<!DOCTYPE html>
<html lang="en">
<head>
<meta charset="utf-8">
<title>Lumora SEO Links</title>
<link href="https://fonts.googleapis.com/css2?family=Montserrat:wght@400;500;600;700;800&family=Open+Sans:wght@400;600&display=swap" rel="stylesheet">
<style>
:root{
  --blue:#2a7be6;
  --blue-deep:#1546c9;
  --blue-dark:#0d3a9a;
  --orange:#f26a1b;
  --orange-light:#ff9a1f;
  --ink:#1e2432;
  --text:#5b6272;
  --line:#d6dde8;
  --pale:#eef3fb;
  --white:#ffffff;
}
*{box-sizing:border-box;margin:0;padding:0}
html,body{width:1200px;height:4816px;overflow:hidden}
body{position:relative;background:var(--white);font-family:"Open Sans",sans-serif;color:var(--text)}
.section{position:absolute;left:0;width:1200px}
h1,h2,h3,h4,.brand,.btn{font-family:"Montserrat",sans-serif}
.btn{display:inline-block;border-radius:30px;font-weight:700;font-size:14px;letter-spacing:1px;text-transform:uppercase}
.btn-solid{background:var(--orange);color:var(--white);padding:14px 34px}
.btn-outline{border:2px solid var(--orange);color:var(--orange);padding:9px 26px;font-size:12px}
.section-title{font-size:34px;font-weight:700;color:var(--ink);text-align:center}
.art{position:absolute;border-radius:24px}

/* hero */
.hero{top:0;height:900px;background:linear-gradient(120deg,var(--blue-deep) 0%,var(--blue) 60%,#3f9cf3 100%);overflow:hidden}
.nav{position:absolute;top:24px;left:120px;right:120px;display:flex;justify-content:space-between;align-items:center}
.brand{font-size:40px;font-weight:800;color:var(--white);display:flex;align-items:center;gap:10px}
.brand-dot{width:14px;height:14px;background:var(--white);border-radius:50%}
.nav-links{display:flex;gap:46px;font-family:"Montserrat",sans-serif;font-size:14px;font-weight:600;color:var(--white);letter-spacing:.5px}
.nav-links span:first-child{border-bottom:2px solid var(--white);padding-bottom:4px}
.hero-copy{position:absolute;left:120px;top:220px;width:460px;color:var(--white)}
.hero-copy h1{font-size:72px;line-height:1.05;font-weight:800}
.hero-copy p{margin:22px 0 30px;font-size:16px;line-height:1.55;opacity:.9}
.hero-art{right:40px;top:70px;width:620px;height:720px;background:linear-gradient(150deg,#7fc4ff 0%,#3b8df0 55%,#1e56d2 100%);opacity:.85}
.wave{position:absolute;left:0;width:1200px;display:block;z-index:0}

/* about */
.about{top:820px;height:440px}
.about-art{left:110px;top:0;width:450px;height:390px;background:linear-gradient(160deg,#e3edff,#9ec3ff 60%,#ffb073)}
.about-copy{position:absolute;left:610px;top:70px;width:470px}
.about-copy h2{font-size:30px;font-weight:700;color:var(--ink);line-height:1.3}
.rule{width:70px;height:4px;background:var(--blue);margin:18px 0 22px}
.about-copy p{font-size:14px;line-height:1.7;margin-bottom:16px}

/* services */
.services{top:1290px;height:660px;background:var(--pale);z-index:1}
.services .section-title{position:absolute;top:80px;left:0;right:0;z-index:2}
.svc{position:absolute;z-index:2;border-radius:50%;background:var(--white);box-shadow:0 10px 40px rgba(20,60,140,.12);text-align:center;display:flex;flex-direction:column;align-items:center;justify-content:center;padding:0 70px}
.svc-icon{width:90px;height:90px;border-radius:50%;background:var(--orange);display:flex;align-items:center;justify-content:center;margin-bottom:22px;border:8px solid #ffe1cf}
.svc h3{font-size:20px;font-weight:700;color:var(--ink);margin-bottom:12px;line-height:1.3}
.svc p{font-size:13px;line-height:1.6}
.svc-a{left:80px;top:210px;width:360px;height:360px}
.svc-b{left:400px;top:170px;width:400px;height:440px;z-index:3;background:var(--blue);border:10px solid var(--orange);box-shadow:0 0 0 6px #ffffff,0 14px 40px rgba(20,60,140,.2);color:var(--white)}
.svc-b h3,.svc-b p{color:var(--white)}
.svc-b .svc-icon{background:transparent;border:3px solid var(--white)}
.svc-c{left:760px;top:210px;width:360px;height:360px}

/* blogs */
.blogs{top:1960px;height:560px}
.blogs .section-title{position:absolute;top:80px;left:0;right:0}
.cards{position:absolute;top:150px;left:128px;display:flex;gap:12px}
.card{width:306px;height:400px;background:var(--white);box-shadow:0 6px 24px rgba(20,40,90,.12);text-align:center}
.card-img{height:210px}
.card .date{display:inline-block;margin-top:-14px;position:relative;background:var(--orange);color:var(--white);font-family:"Montserrat",sans-serif;font-size:11px;font-weight:700;padding:6px 18px;border-radius:3px}
.card h4{font-size:15px;font-weight:700;color:var(--ink);line-height:1.4;margin:16px 28px 8px}
.card p{font-size:12px;line-height:1.5;margin:0 30px 16px}

/* testimonials */
.testimonials{top:2520px;height:760px}
.testimonials .band{position:absolute;top:0;left:0;width:1200px;height:760px}
.testimonials .section-title{position:absolute;top:156px;left:0;right:0;color:var(--white)}
.quotes{position:absolute;top:280px;left:128px;display:flex}
.quote{width:315px;height:260px;border:1px solid rgba(255,255,255,.6);color:var(--white);text-align:center;padding:56px 30px 0;position:relative}
.quote.is-active{background:var(--white);color:var(--text);box-shadow:0 10px 30px rgba(0,0,0,.15);height:290px;margin-top:-14px}
.avatar{position:absolute;top:-34px;left:50%;margin-left:-34px;width:68px;height:68px;border-radius:50%;border:4px solid var(--white);background:linear-gradient(160deg,#d9b08c,#8a5a3c)}
.quote p{font-size:13px;line-height:1.6}
.quote h4{margin-top:20px;font-size:13px;font-weight:700;letter-spacing:1px;color:inherit}
.quote.is-active h4{color:var(--ink)}
.dots{position:absolute;top:568px;left:0;right:0;display:flex;justify-content:center;gap:10px}
.dots span{width:12px;height:12px;border-radius:50%;background:rgba(255,255,255,.5)}
.dots span:first-child{background:var(--white)}

/* faq */
.faq{top:3300px;height:560px}
.faq .section-title{position:absolute;top:52px;left:0;right:0}
.faq-art{left:80px;top:150px;width:460px;height:390px;background:linear-gradient(150deg,#c9dcff,#3b7cf0 60%,#f57a2e)}
.faq-list{position:absolute;left:560px;top:132px;width:512px}
.faq-item{border:1px solid var(--line);border-radius:6px;margin-bottom:14px;padding:0 50px 0 22px;height:50px;display:flex;align-items:center;font-size:13px;color:var(--ink);position:relative}
.faq-item::after{content:"";position:absolute;right:18px;top:50%;width:16px;height:16px;margin-top:-8px;border:1.5px solid #9aa6b8;border-radius:50%}
.faq-item.is-open{display:block;height:auto;background:var(--pale);padding:22px 50px 24px 22px}
.faq-item.is-open::after{top:30px}
.faq-item.is-open h4{font-size:14px;font-weight:700;margin-bottom:14px}
.faq-item.is-open p{font-size:13px;line-height:1.6;color:var(--text)}

/* contact */
.contact{top:3860px;height:560px;background:linear-gradient(120deg,var(--blue-deep),var(--blue) 70%,#3f9cf3)}
.contact .section-title{position:absolute;top:100px;left:0;right:0;color:var(--white)}
.form{position:absolute;top:190px;left:190px;width:820px}
.row{display:flex;gap:20px;margin-bottom:20px}
.field{flex:1;height:44px;background:var(--white);border-radius:22px;padding:0 22px;display:flex;align-items:center;font-size:13px;color:#4a5060}
.field.area{height:120px;border-radius:16px;align-items:flex-start;padding-top:14px}
.form .btn{display:block;width:236px;margin:16px auto 0;text-align:center;padding:15px 0}

/* footer */
.footer{top:4420px;height:396px;background:var(--white)}
.footer .brand{position:absolute;left:128px;top:130px;color:var(--blue)}
.footer .brand .brand-dot{background:var(--blue)}
.socials{position:absolute;left:128px;top:230px;display:flex;gap:10px}
.socials span{width:30px;height:30px;border-radius:50%;background:var(--blue)}
.copyright{position:absolute;left:128px;top:280px;font-size:12px;line-height:1.6}
.col{position:absolute;top:112px;font-size:13px;line-height:2.3}
.col h4{font-size:14px;font-weight:700;color:var(--ink);letter-spacing:.5px;margin-bottom:8px}
.col-info{left:412px}
.col-links{left:628px}
.col-contact{left:820px}
.contact-line{display:flex;gap:14px;margin-bottom:14px;line-height:1.5}
.contact-line svg{flex:none;margin-top:4px}
.contact-line b{display:block;font-family:"Montserrat",sans-serif;font-size:11px;color:var(--ink)}
</style>
</head>
<body>

<header class="section hero">
  <div class="art hero-art" role="img" aria-label="Isometric illustration of people working on large floating SEO dashboards"></div>
  <nav class="nav">
    <div class="brand"><span class="brand-dot"></span>Lumora</div>
    <div class="nav-links"><span>HOME</span><span>ABOUT US</span><span>SERVICES</span><span>TESTIMONIALS</span><span>FAQ</span><span>CONTACT</span></div>
  </nav>
  <div class="hero-copy">
    <h1>Lumora<br>SEO links</h1>
    <p>Lorem ipsum dolor sit amet, consectetur adipiscing elit, sed do eiusmod tempor incididunt ut labore.</p>
    <span class="btn btn-solid">Get started</span>
  </div>
  <svg class="wave" style="bottom:0" height="180" viewBox="0 0 1200 180" preserveAspectRatio="none"><path d="M0 90 C300 200 520 30 800 80 C980 115 1100 60 1200 40 L1200 180 L0 180 Z" fill="#ffffff"/></svg>
</header>

<section class="section about">
  <div class="art about-art" role="img" aria-label="Illustration of a person building a web page with link and chart elements"></div>
  <div class="about-copy">
    <h2>Lorem ipsum dolor sit amet consectetuer</h2>
    <div class="rule"></div>
    <p>Lorem ipsum dolor sit amet, consectetur adipiscing elit, sed do eiusmod tempor incididunt ut labore et dolore magna aliqua. Ut enim ad minim veniam, quis nostrud exercitation ullamco laboris nisi ut aliquip ex ea commodo consequat. Duis aute irure dolor in reprehenderit.</p>
    <p>Sed ut perspiciatis unde omnis iste natus error sit voluptatem accusantium doloremque laudantium, totam rem aperiam eaque ipsa quae ab illo inventore.</p>
    <span class="btn btn-outline">Learn more</span>
  </div>
</section>

<section class="section services">
  <svg class="wave" style="top:-60px" height="80" viewBox="0 0 1200 80" preserveAspectRatio="none"><path d="M0 80 C300 0 900 0 1200 80 Z" fill="#eef3fb"/></svg>
  <h2 class="section-title">Lumora Services</h2>
  <div class="svc svc-a">
    <div class="svc-icon"><svg width="34" height="34" viewBox="0 0 24 24" fill="none" stroke="#fff" stroke-width="2"><path d="M12 2l3 6.5 7 .8-5.2 4.8 1.4 7L12 17.6 5.8 21l1.4-7L2 9.3l7-.8z"/></svg></div>
    <h3>Premium Links</h3>
    <p>Lorem ipsum dolor sit amet, consectetur adipiscing elit, sed do eiusmod tempor incididunt.</p>
  </div>
  <div class="svc svc-b">
    <div class="svc-icon"><svg width="38" height="38" viewBox="0 0 24 24" fill="none" stroke="#fff" stroke-width="2"><rect x="3" y="5" width="18" height="16" rx="2"/><path d="M3 10h18M8 3v4M16 3v4"/></svg></div>
    <h3>Monthly Links<br>Subscription</h3>
    <p>Lorem ipsum dolor sit amet, consectetur adipiscing elit, sed do eiusmod tempor incididunt.</p>
  </div>
  <div class="svc svc-c">
    <div class="svc-icon"><svg width="34" height="34" viewBox="0 0 24 24" fill="none" stroke="#fff" stroke-width="2"><path d="M10 14a4 4 0 0 0 5.7 0l3-3a4 4 0 0 0-5.7-5.7l-1 1"/><path d="M14 10a4 4 0 0 0-5.7 0l-3 3a4 4 0 0 0 5.7 5.7l1-1"/></svg></div>
    <h3>Link Insertions</h3>
    <p>Lorem ipsum dolor sit amet, consectetur adipiscing elit, sed do eiusmod tempor incididunt.</p>
  </div>
  <svg class="wave" style="bottom:-60px" height="80" viewBox="0 0 1200 80" preserveAspectRatio="none"><path d="M0 0 C300 80 900 80 1200 0 Z" fill="#eef3fb"/></svg>
</section>

<section class="section blogs">
  <h2 class="section-title">Blogs &amp; News</h2>
  <div class="cards">
    <article class="card">
      <div class="card-img" role="img" aria-label="Photo of a laptop with digital marketing graphics" style="background:linear-gradient(135deg,#7ab0e8,#2d5a9c)"></div>
      <span class="date">12 SEP 2020</span>
      <h4>Lorem ipsum dolor sit amet, consectetur adipiscing</h4>
      <p>Sed do eiusmod tempor incididunt ut labore et dolore magna.</p>
      <span class="btn btn-outline">Learn more</span>
    </article>
    <article class="card">
      <div class="card-img" role="img" aria-label="Photo of a hand touching a search screen" style="background:linear-gradient(135deg,#9aa4b4,#3c4658)"></div>
      <span class="date">12 SEP 2020</span>
      <h4>Lorem ipsum dolor sit amet, consectetur adipiscing</h4>
      <p>Sed do eiusmod tempor incididunt ut labore et dolore magna.</p>
      <span class="btn btn-outline">Learn more</span>
    </article>
    <article class="card">
      <div class="card-img" role="img" aria-label="Photo of glowing blue digital SEO interface" style="background:linear-gradient(135deg,#1c3d6e,#0a1a33)"></div>
      <span class="date">12 SEP 2020</span>
      <h4>Lorem ipsum dolor sit amet, consectetur adipiscing</h4>
      <p>Sed do eiusmod tempor incididunt ut labore et dolore magna.</p>
      <span class="btn btn-outline">Learn more</span>
    </article>
  </div>
</section>

<section class="section testimonials">
  <svg class="band" viewBox="0 0 1200 760" preserveAspectRatio="none">
    <defs><linearGradient id="orangeBand" x1="0" y1="0" x2="1" y2="0"><stop offset="0" stop-color="#f05a14"/><stop offset="1" stop-color="#ff9a1f"/></linearGradient></defs>
    <path d="M0 60 C250 0 450 140 700 90 C900 50 1050 20 1200 70 L1200 690 C1000 760 750 650 500 700 C300 740 150 720 0 690 Z" fill="url(#orangeBand)"/>
  </svg>
  <h2 class="section-title">Client Testimonials</h2>
  <div class="quotes">
    <div class="quote">
      <div class="avatar" role="img" aria-label="Client portrait"></div>
      <p>Lorem ipsum dolor sit amet, consectetur adipiscing elit, sed do eiusmod tempor incididunt ut labore et dolore magna aliqua ut enim.</p>
      <h4>MARCUS HALE</h4>
    </div>
    <div class="quote is-active">
      <div class="avatar" role="img" aria-label="Client portrait" style="background:linear-gradient(160deg,#c9a487,#5a4636)"></div>
      <p>Lorem ipsum dolor sit amet, consectetur adipiscing elit, sed do eiusmod tempor incididunt ut labore et dolore magna aliqua ut enim.</p>
      <h4>OWEN PRATT</h4>
    </div>
    <div class="quote">
      <div class="avatar" role="img" aria-label="Client portrait" style="background:linear-gradient(160deg,#e0b896,#6b4030)"></div>
      <p>Lorem ipsum dolor sit amet, consectetur adipiscing elit, sed do eiusmod tempor incididunt ut labore et dolore magna aliqua ut enim.</p>
      <h4>LENA FORSYTH</h4>
    </div>
  </div>
  <div class="dots"><span></span><span></span><span></span></div>
</section>

<section class="section faq">
  <h2 class="section-title">Frequently Asked Questions</h2>
  <div class="art faq-art" role="img" aria-label="Illustration of a team working around a large SEO sign and charts"></div>
  <div class="faq-list">
    <div class="faq-item is-open">
      <h4>Lorem ipsum dolor sit amet, consectetur adipiscing elit ?</h4>
      <p>Sed ut perspiciatis unde omnis iste natus error sit voluptatem accusantium doloremque laudantium, totam rem aperiam, eaque ipsa quae ab illo inventore veritatis et quasi architecto beatae vitae dicta sunt explicabo nemo enim.</p>
    </div>
    <div class="faq-item">Sed ut perspiciatis unde omnis iste natus ?</div>
    <div class="faq-item">Error sit voluptatem accusantium doloremque laudantium ?</div>
    <div class="faq-item">Totam rem aperiam, eaque ipsa quae ab illo inventore ?</div>
    <div class="faq-item">Nemo enim ipsam voluptatem quia voluptas sit ?</div>
  </div>
</section>

<section class="section contact">
  <svg class="wave" style="top:-1px" height="90" viewBox="0 0 1200 90" preserveAspectRatio="none"><path d="M0 0 L1200 0 L1200 20 C900 90 300 90 0 20 Z" fill="#ffffff"/></svg>
  <h2 class="section-title">Got Questions?</h2>
  <div class="form">
    <div class="row"><div class="field">First Name*</div><div class="field">Last Name*</div></div>
    <div class="row"><div class="field">Contact Number*</div><div class="field">E-mail*</div></div>
    <div class="row"><div class="field area">Leave a Message</div></div>
    <span class="btn btn-solid">Send message</span>
  </div>
  <svg class="wave" style="bottom:-1px" height="70" viewBox="0 0 1200 70" preserveAspectRatio="none"><path d="M0 70 C300 10 900 10 1200 70 Z" fill="#ffffff"/></svg>
</section>

<footer class="section footer">
  <div class="brand"><span class="brand-dot"></span>Lumora</div>
  <div class="socials"><span></span><span></span><span></span><span></span><span></span></div>
  <p class="copyright">Copyright © 2020 Lumora.<br>All Right Reserved</p>
  <div class="col col-info">
    <h4>INFORMATION</h4>
    Home<br>About Us<br>Services<br>News &amp; Blogs<br>Contact
  </div>
  <div class="col col-links">
    <h4>LINKS</h4>
    Careers<br>Support<br>Sitemap<br>Privacy Policy<br>Terms of Use
  </div>
  <div class="col col-contact">
    <h4>CONTACT</h4>
    <div class="contact-line"><svg width="16" height="16" viewBox="0 0 24 24" fill="#2a7be6"><path d="M12 2a7 7 0 0 0-7 7c0 5 7 13 7 13s7-8 7-13a7 7 0 0 0-7-7zm0 9.5a2.5 2.5 0 1 1 0-5 2.5 2.5 0 0 1 0 5z"/></svg><span><b>ADDRESS</b>2140 Fern Hollow Drive, Westbrook</span></div>
    <div class="contact-line"><svg width="16" height="16" viewBox="0 0 24 24" fill="#2a7be6"><path d="M6.6 10.8a15 15 0 0 0 6.6 6.6l2.2-2.2c.3-.3.7-.4 1-.2 1.1.4 2.3.6 3.6.6.6 0 1 .4 1 1V20c0 .6-.4 1-1 1A17 17 0 0 1 3 4c0-.6.4-1 1-1h3.5c.6 0 1 .4 1 1 0 1.3.2 2.5.6 3.6.1.3 0 .7-.2 1z"/></svg><span><b>PHONE</b>(555) 230-2214</span></div>
    <div class="contact-line"><svg width="16" height="16" viewBox="0 0 24 24" fill="#2a7be6"><path d="M3 5h18v14H3z" fill="none" stroke="#2a7be6" stroke-width="2"/><path d="M3 6l9 7 9-7" fill="none" stroke="#2a7be6" stroke-width="2"/></svg><span><b>EMAIL US</b>hello@lumora.com</span></div>
  </div>
</footer>

</body>
</html>
```